Flyer for Children Therapy Center

We need a flyer with front and back with the following services:

Services:
- Fisioterapia (File 3: B.jpg)
- Terapia Ocupacional (G.jpg)
- Terapia da Fala (H.jpg)
- Musicoterapia (File 4: C.jpg)
- Estimulação Elétrica Neurofuncional (File 2: molli.jpg)
- Entre outros!

Products:
- Fitoterapia Tradicional Chinesa (I.jpg)
- Ortóteses dinâmicas funcionais (Before: E.1.jpg, After: E.2.jpg)
- Fato de compressão dinâmica sob medida (Before: F.1.jpg, After: F.2.jpg)
- Assento pélvico moldado com técnica exclusiva (File 5: D.jpg)

Target Market(s)

Parents of children with special needs

Colors

Designer to choose colors to be used in the design.

Requirements
Must have
• The flyer must have:
• - Our logo
• - Company Name: Ninho do Vale
• - center description: Centro de Terapias Especializadas para crianças e jovens.
• - Slogan: Semeamos amor, colhemos sorrisos, distribuímos vitórias!
• - Site: www.ninvale.pt
• - Facebook: www.ninvale.pt/comunidade
• - Cellular phone: +351 913 000 417
• - Land Line: +351 219 000 542
• - E-mail: geral@ninvale.pt
• - Address: R. Henrique Vilaça Ramos 12B, 2600-917 - Vila Serena, Terra Alta
Nice to have
• Logo colors
Should not have
• Dark colors.

```html
<!DOCTYPE html>
<html lang="pt">
<head>
<meta charset="utf-8">
<title>Ninho do Vale – Flyer</title>
<link rel="stylesheet" href="https://fonts.googleapis.com/css2?family=Nunito:wght@400;600;700;800;900&display=swap">
<style>
  :root {
    --teal: #2fb5a2;
    --purple: #7a3f88;
    --red: #e33d3b;
    --yellow: #f6cd1e;
    --dark: #3d3d40;
    --white: #ffffff;
    --ink: #2c2c2e;
    --backdrop: #efe9e1;
  }
  html, body {
    margin: 0;
    width: 1200px;
    height: 1200px;
    overflow: hidden;
    background: var(--backdrop);
    font-family: "Nunito", sans-serif;
  }
  .sheet {
    position: absolute;
    top: 243px;
    width: 552px;
    height: 715px;
    box-shadow: 0 4px 14px rgba(0,0,0,.18);
  }
  .sheet--front { left: 36px; }
  .sheet--back { left: 612px; }
  .sheet svg { display: block; width: 552px; height: 715px; }
  .sheet text { font-family: "Nunito", sans-serif; }
  .brand-name { font-weight: 800; fill: var(--ink); }
  .slogan { font-weight: 900; }
  .label { font-weight: 600; fill: var(--white); }
  .label--strong { font-weight: 800; }
  .caption { font-weight: 700; }
  .contact { font-weight: 400; fill: var(--white); font-size: 9.5px; }
</style>
</head>
<body>

<!-- Front page -->
<div class="sheet sheet--front">
<svg viewBox="0 0 644 834" xmlns="http://www.w3.org/2000/svg">
  <defs>
    <linearGradient id="front-hero" x1="0" y1="0" x2="1" y2="1">
      <stop offset="0" stop-color="#9fd3e4"/><stop offset=".55" stop-color="#d9dde0"/><stop offset="1" stop-color="#8fc7a8"/>
    </linearGradient>
    <linearGradient id="tone-ball" x1="0" y1="0" x2="0" y2="1">
      <stop offset="0" stop-color="#f1d8c8"/><stop offset="1" stop-color="#3566b8"/>
    </linearGradient>
    <linearGradient id="tone-play" x1="0" y1="0" x2="1" y2="1">
      <stop offset="0" stop-color="#f4f1ec"/><stop offset="1" stop-color="#e6a93a"/>
    </linearGradient>
    <linearGradient id="tone-speech" x1="0" y1="0" x2="1" y2="1">
      <stop offset="0" stop-color="#f3ebe0"/><stop offset="1" stop-color="#c8b7a1"/>
    </linearGradient>
    <linearGradient id="tone-music" x1="0" y1="0" x2="1" y2="1">
      <stop offset="0" stop-color="#6b4a3a"/><stop offset="1" stop-color="#e58aa9"/>
    </linearGradient>
    <linearGradient id="tone-suit" x1="0" y1="0" x2="1" y2="1">
      <stop offset="0" stop-color="#e4ece9"/><stop offset="1" stop-color="#4a4a4e"/>
    </linearGradient>
  </defs>

  <rect width="644" height="834" fill="var(--white)"/>

  <!-- background bands -->
  <polygon points="0,380 644,335 644,600 330,560 0,470" fill="var(--purple)"/>
  <polygon points="0,470 330,560 644,600 300,665 0,700" fill="var(--teal)"/>
  <polygon points="0,640 240,665 644,780 0,780" fill="var(--yellow)"/>

  <!-- hero photo -->
  <polygon points="0,0 340,0 412,365 0,395" fill="url(#front-hero)" role="img" aria-label="Photo: therapist guiding a child through a play tunnel in a therapy room"/>
  <polygon points="340,0 356,0 428,364 412,366" fill="var(--purple)"/>

  <!-- brand -->
  <circle cx="445" cy="140" r="9" fill="var(--teal)"/>
  <text class="brand-name" x="462" y="148" font-size="22">Ninho do Vale</text>

  <!-- slogan -->
  <text class="slogan" x="510" y="190" font-size="22" text-anchor="middle" fill="var(--teal)">Semeamos amor,</text>
  <text class="slogan" x="510" y="216" font-size="20" text-anchor="middle" fill="var(--ink)">colhemos sorrisos,</text>
  <text class="slogan" x="510" y="239" font-size="18" text-anchor="middle" fill="var(--red)">distribuímos vitórias!</text>

  <text x="512" y="278" font-size="11.5" text-anchor="middle" fill="var(--ink)" font-weight="600">Centro de Terapias Especializadas</text>
  <text x="512" y="300" font-size="17.5" text-anchor="middle" fill="var(--ink)">para crianças e jovens</text>

  <!-- services heading -->
  <path d="M463,400 H644 V428 H463 A14,14 0 0 1 463,400 Z" fill="var(--teal)"/>
  <text x="556" y="420" font-size="15" font-weight="800" text-anchor="middle" fill="var(--yellow)">Our Services:</text>

  <g class="service-list">
    <text class="label" x="555" y="459" font-size="12" text-anchor="end">Terapia da Fala</text>
    <circle cx="568" cy="455" r="5.5" fill="none" stroke="#fff" stroke-width="1.3"/>
    <path d="M565.5,455 l2,2 l3.5,-4" fill="none" stroke="#fff" stroke-width="1.3"/>
    <text class="label" x="555" y="480" font-size="12" text-anchor="end">Musicoterapia</text>
    <circle cx="568" cy="476" r="5.5" fill="none" stroke="#fff" stroke-width="1.3"/>
    <path d="M565.5,476 l2,2 l3.5,-4" fill="none" stroke="#fff" stroke-width="1.3"/>
  </g>

  <!-- hexagon photos -->
  <polygon points="145,355 231.6,405 231.6,505 145,555 58.4,505 58.4,405" fill="url(#tone-ball)" stroke="var(--teal)" stroke-width="9" stroke-linejoin="round" role="img" aria-label="Photo: child leaning over a therapy ball"/>
  <polygon points="292,378 363,419 363,501 292,542 221,501 221,419" fill="url(#tone-play)" stroke="var(--red)" stroke-width="8" stroke-linejoin="round" role="img" aria-label="Photo: child in a supported standing frame during physiotherapy"/>
  <polygon points="413,485 489.2,529 489.2,617 413,661 336.8,617 336.8,529" fill="url(#tone-speech)" stroke="var(--purple)" stroke-width="8" stroke-linejoin="round" role="img" aria-label="Photo: speech therapist working with a child at a table"/>
  <polygon points="535,518 614.7,564 614.7,656 535,702 455.3,656 455.3,564" fill="url(#tone-music)" stroke="var(--red)" stroke-width="8" stroke-linejoin="round" role="img" aria-label="Photo: music therapist playing guitar with a child"/>
  <polygon points="102,604 178.2,648 178.2,736 102,780 25.8,736 25.8,648" fill="url(#tone-suit)" stroke="var(--purple)" stroke-width="8" stroke-linejoin="round" role="img" aria-label="Photo: child wearing a neurofunctional stimulation suit"/>

  <!-- services on teal -->
  <g>
    <circle cx="61" cy="572" r="5.5" fill="none" stroke="#fff" stroke-width="1.3"/>
    <path d="M58.5,572 l2,2 l3.5,-4" fill="none" stroke="#fff" stroke-width="1.3"/>
    <text class="label" x="71" y="576" font-size="12">Terapia Ocupacional</text>
    <circle cx="231" cy="572" r="5.5" fill="none" stroke="#fff" stroke-width="1.3"/>
    <path d="M228.5,572 l2,2 l3.5,-4" fill="none" stroke="#fff" stroke-width="1.3"/>
    <text class="label" x="241" y="576" font-size="12">Fisioterapia</text>
  </g>

  <!-- services on yellow -->
  <g>
    <circle cx="195" cy="731" r="5.5" fill="none" stroke="var(--ink)" stroke-width="1.3"/>
    <path d="M192.5,731 l2,2 l3.5,-4" fill="none" stroke="var(--ink)" stroke-width="1.3"/>
    <text x="205" y="735" font-size="12" font-weight="600" fill="var(--ink)">Estimulação Elétrica Neurofuncional</text>
    <circle cx="195" cy="752" r="5.5" fill="none" stroke="var(--ink)" stroke-width="1.3"/>
    <path d="M192.5,752 l2,2 l3.5,-4" fill="none" stroke="var(--ink)" stroke-width="1.3"/>
    <text x="205" y="756" font-size="12" font-weight="600" fill="var(--ink)">Entre outros!</text>
  </g>

  <!-- footer -->
  <rect x="0" y="780" width="644" height="54" fill="var(--dark)"/>
  <path d="M44,799 a5,5 0 0 1 10,0 c0,4 -5,9 -5,9 s-5,-5 -5,-9 z" fill="none" stroke="#fff" stroke-width="1.5"/>
  <circle cx="49" cy="799" r="1.6" fill="#fff"/>
  <text class="contact" x="58" y="809">R. Henrique Vilaça Ramos 12B, 2600-917 - Vila Serena, Terra Alta</text>
  <rect x="392" y="798" width="7" height="12" rx="1.5" fill="none" stroke="#fff" stroke-width="1.3"/>
  <text class="contact" x="404" y="810">+351 913 000 417</text>
  <path d="M508,802 q8,-5 16,0 l-2,3 h-3 v-1 h-6 v1 h-3 z M511,806 h10 l2,5 h-14 z" fill="#fff"/>
  <text class="contact" x="530" y="810">+351 219 000 542</text>
</svg>
</div>

<!-- Back page -->
<div class="sheet sheet--back">
<svg viewBox="0 0 644 834" xmlns="http://www.w3.org/2000/svg">
  <defs>
    <linearGradient id="tone-seat-a" x1="0" y1="0" x2="1" y2="1">
      <stop offset="0" stop-color="#e9e5e0"/><stop offset="1" stop-color="#5a6a86"/>
    </linearGradient>
    <linearGradient id="tone-seat-b" x1="0" y1="0" x2="1" y2="1">
      <stop offset="0" stop-color="#e7e2d9"/><stop offset="1" stop-color="#d2352c"/>
    </linearGradient>
    <linearGradient id="tone-feet-a" x1="0" y1="0" x2="0" y2="1">
      <stop offset="0" stop-color="#9c9895"/><stop offset="1" stop-color="#d9a897"/>
    </linearGradient>
    <linearGradient id="tone-feet-b" x1="0" y1="0" x2="0" y2="1">
      <stop offset="0" stop-color="#7ab56a"/><stop offset="1" stop-color="#e3b19f"/>
    </linearGradient>
    <linearGradient id="tone-suit-a" x1="0" y1="0" x2="1" y2="1">
      <stop offset="0" stop-color="#5a3b2c"/><stop offset="1" stop-color="#e9c2ad"/>
    </linearGradient>
    <linearGradient id="tone-suit-b" x1="0" y1="0" x2="1" y2="1">
      <stop offset="0" stop-color="#4b3528"/><stop offset="1" stop-color="#2b4f86"/>
    </linearGradient>
    <linearGradient id="tone-yellow" x1="0" y1="0" x2="1" y2="1">
      <stop offset="0" stop-color="#4a3a2c"/><stop offset="1" stop-color="#d9bd2c"/>
    </linearGradient>
    <linearGradient id="tone-mat" x1="0" y1="0" x2="1" y2="1">
      <stop offset="0" stop-color="#e2c237"/><stop offset="1" stop-color="#58a86a"/>
    </linearGradient>
  </defs>

  <rect width="644" height="834" fill="var(--red)"/>
  <polygon points="0,370 644,220 644,700 0,515" fill="var(--white)"/>
  <polygon points="0,200 40,185 40,345 0,360" fill="var(--teal)"/>
  <polygon points="0,515 644,700 644,834 0,834" fill="var(--dark)"/>
  <polygon points="540,700 644,650 644,730" fill="var(--purple)"/>

  <!-- heading -->
  <line x1="38" y1="48" x2="256" y2="48" stroke="#fff" stroke-width="1.5"/>
  <line x1="388" y1="48" x2="606" y2="48" stroke="#fff" stroke-width="1.5"/>
  <polygon points="266,38 382,38 376,58 260,58" fill="var(--yellow)"/>
  <text x="321" y="53" font-size="14" font-weight="900" text-anchor="middle" fill="var(--ink)">PRODUCTS</text>

  <text class="label label--strong" x="38" y="80" font-size="12.5">Assento pélvico moldado com técnica exclusiva</text>
  <text class="label label--strong" x="378" y="80" font-size="12.5">Ortóteses dinâmicas funcionais</text>

  <!-- pelvic seat -->
  <g>
    <rect x="38" y="95" width="272" height="270" rx="10" fill="var(--purple)" stroke="var(--dark)" stroke-width="2"/>
    <path d="M39,105 a9,9 0 0 1 9,-9 H170 V340 H39 Z" fill="url(#tone-seat-a)" role="img" aria-label="Photo before: child seated without pelvic seat support"/>
    <path d="M172,96 H300 a9,9 0 0 1 9,9 V340 H172 Z" fill="url(#tone-seat-b)" role="img" aria-label="Photo after: child seated upright on moulded pelvic seat"/>
    <text class="label" x="104" y="357" font-size="12.5" text-anchor="middle">Before</text>
    <text class="label" x="240" y="357" font-size="12.5" text-anchor="middle">After</text>
  </g>

  <!-- orthoses -->
  <g>
    <rect x="348" y="95" width="257" height="127" rx="10" fill="var(--yellow)" stroke="var(--dark)" stroke-width="2"/>
    <path d="M349,105 a9,9 0 0 1 9,-9 H595 a9,9 0 0 1 9,9 V200 H349 Z" fill="url(#tone-feet-a)" role="img" aria-label="Photo before: bare feet standing without orthoses"/>
    <text class="caption" x="476" y="215" font-size="12.5" text-anchor="middle" fill="var(--ink)">Before</text>
    <rect x="348" y="238" width="257" height="127" rx="10" fill="var(--yellow)" stroke="var(--dark)" stroke-width="2"/>
    <path d="M349,248 a9,9 0 0 1 9,-9 H595 a9,9 0 0 1 9,9 V343 H349 Z" fill="url(#tone-feet-b)" role="img" aria-label="Photo after: feet standing aligned after dynamic orthoses"/>
    <text class="caption" x="476" y="358" font-size="12.5" text-anchor="middle" fill="var(--ink)">After</text>
  </g>

  <!-- compression suit -->
  <g>
    <rect x="38" y="378" width="272" height="254" rx="10" fill="var(--teal)" stroke="var(--dark)" stroke-width="2"/>
    <path d="M39,388 a9,9 0 0 1 9,-9 H174 V612 H39 Z" fill="url(#tone-suit-a)" role="img" aria-label="Photo before: child's back without compression suit"/>
    <path d="M178,379 H300 a9,9 0 0 1 9,9 V612 H178 Z" fill="url(#tone-suit-b)" role="img" aria-label="Photo after: child wearing a blue dynamic compression suit"/>
    <rect x="174" y="379" width="4" height="252" fill="#fff"/>
    <text class="caption" x="106" y="627" font-size="12.5" text-anchor="middle" fill="var(--ink)">Before</text>
    <text class="caption" x="240" y="627" font-size="12.5" text-anchor="middle" fill="var(--ink)">After</text>
  </g>

  <!-- suit sequence -->
  <g>
    <rect x="348" y="378" width="257" height="252" rx="10" fill="#fff" stroke="var(--dark)" stroke-width="2"/>
    <path d="M349,388 a9,9 0 0 1 9,-9 H474 V629 H358 a9,9 0 0 1 -9,-9 Z" fill="url(#tone-yellow)" role="img" aria-label="Photo: child in yellow shirt seen from behind"/>
    <path d="M478,379 H595 a9,9 0 0 1 9,9 V502 H478 Z" fill="url(#tone-mat)" role="img" aria-label="Photo: child sitting on a play mat"/>
    <path d="M478,506 H604 V620 a9,9 0 0 1 -9,9 H478 Z" fill="url(#tone-mat)" role="img" aria-label="Photo: child crawling on a play mat"/>
  </g>

  <text class="label label--strong" x="55" y="654" font-size="12.5">Fato de compressão dinâmica sob medida</text>

  <!-- contacts -->
  <g>
    <path d="M38,720 a4.5,4.5 0 0 1 9,0 c0,4 -4.5,8 -4.5,8 s-4.5,-4 -4.5,-8 z" fill="none" stroke="#fff" stroke-width="1.4"/>
    <text class="contact" x="54" y="725" font-size="9">R. Henrique Vilaça Ramos 12B,</text>
    <text class="contact" x="54" y="736" font-size="9">2600-917 - Vila Serena, Terra Alta</text>

    <rect x="39" y="749" width="7" height="11" rx="1.5" fill="none" stroke="#fff" stroke-width="1.3"/>
    <text class="contact" x="54" y="759" font-size="9">+351 913 000 417</text>
    <path d="M139,752 q7,-4 14,0 l-2,3 h-2 v-1 h-6 v1 h-2 z M141,756 h10 l2,4 h-14 z" fill="#fff"/>
    <text class="contact" x="158" y="759" font-size="9">+351 219 000 542</text>

    <circle cx="42.5" cy="774" r="5" fill="none" stroke="#fff" stroke-width="1.2"/>
    <line x1="37.5" y1="774" x2="47.5" y2="774" stroke="#fff" stroke-width="1"/>
    <ellipse cx="42.5" cy="774" rx="2.2" ry="5" fill="none" stroke="#fff" stroke-width="1"/>
    <text class="contact" x="54" y="777" font-size="9">www.ninvale.pt</text>
    <rect x="139" y="770" width="12" height="8" fill="none" stroke="#fff" stroke-width="1.2"/>
    <path d="M139,770 l6,5 l6,-5" fill="none" stroke="#fff" stroke-width="1.2"/>
    <text class="contact" x="158" y="777" font-size="9">geral@ninvale.pt</text>

    <rect x="38" y="787" width="10" height="10" rx="2" fill="#fff"/>
    <text class="contact" x="54" y="796" font-size="9">www.ninvale.pt/comunidade</text>
  </g>

  <!-- partner badge -->
  <ellipse cx="334" cy="757" rx="66" ry="50" fill="#f3ecd2" stroke="#5f8a3a" stroke-width="4" role="img" aria-label="Partner badge"/>

  <!-- brand seal -->
  <circle cx="493" cy="723" r="73" fill="#fff" stroke="#c9b6d0" stroke-width="2"/>
  <text class="brand-name" x="493" y="729" font-size="16" text-anchor="middle">Ninho do Vale</text>
</svg>
</div>

</body>
</html>
```